VFX Company Business Card Design Project

The Kestrel Works is a decentralized Visual Effects Studio servicing the television and feature film industries.
Project Brief:
Take our logo that was previously designed on Pencil Harbor and make a double sided business card.
Requirements:
- Card MUST be double sided.
- Front of card MUST have the yellow part of our logo against the dark grey background.
- Back of card is completely up to the designer.
- Back of card must include the complete company logo.
Please follow these File Preparation guidelines:
http://printnook.ca/infopage?file=filetype_en&s=PrintNook_new&lang=en
Business

```html
<!DOCTYPE html>
<html lang="en">
<head>
<meta charset="utf-8">
<title>The Kestrel Works — Business Cards</title>
<link rel="stylesheet" href="https://fonts.googleapis.com/css2?family=Jost:wght@400;500;600&display=swap">
<style>
  :root {
    --backdrop: #d9d4cc;
    --card: #262626;
    --card-edge: #111111;
    --yellow: #fcc22a;
    --ink-light: #eef1e6;
    --ink-grey: #5f6a6c;
    --ink-soft: #d9dcd4;
  }
  * { margin: 0; padding: 0; box-sizing: border-box; }
  html, body {
    width: 1200px; height: 727px; overflow: hidden;
    background: var(--backdrop);
    font-family: "Jost", "Futura", sans-serif;
  }
  .sheet { position: relative; width: 1200px; height: 727px; }
  .card {
    position: absolute; width: 526px; height: 299px;
    background: var(--card); border: 1px solid var(--card-edge);
    border-radius: 28px; overflow: hidden;
  }
  .card--front       { left: 68px;  top: 42px; }
  .card--contact     { left: 628px; top: 47px; }
  .card--back-mark   { left: 65px;  top: 383px; }
  .card--back-name   { left: 623px; top: 387px; }

  /* front: name in brand yellow */
  .front-name {
    position: absolute; left: 0; right: 0; top: 0; bottom: 0;
    display: flex; align-items: center; justify-content: center;
    color: var(--yellow); font-weight: 600; font-size: 50px;
    letter-spacing: 1px;
  }

  /* contact side */
  .contact-bar { position: absolute; left: 0; top: 36px; width: 12px; height: 42px; background: var(--ink-light); }
  .person-name { position: absolute; left: 37px; top: 31px; color: var(--ink-light); font-size: 20px; font-weight: 600; }
  .person-title { position: absolute; left: 37px; top: 57px; color: var(--ink-light); font-size: 15px; }
  .address { position: absolute; left: 35px; top: 104px; color: var(--ink-light); font-size: 13.5px; line-height: 18px; }
  .details { position: absolute; left: 35px; top: 170px; list-style: none; color: var(--ink-light); font-size: 14px; }
  .details li { display: flex; align-items: center; gap: 6px; height: 23.5px; }
  .details svg { width: 10px; height: 10px; fill: var(--ink-light); }
  .web-small { position: absolute; left: 35px; top: 259px; color: var(--ink-light); font-size: 13.5px; font-weight: 600; letter-spacing: 1.6px; }
  .web-small .accent { color: var(--ink-grey); }
  .contact-name {
    position: absolute; right: 42px; top: 150px;
    color: var(--ink-grey); font-size: 33px; font-weight: 600; line-height: 1;
    text-align: right;
  }

  /* back with mark */
  .mark-row {
    position: absolute; left: 36px; top: 108px;
    display: flex; align-items: center; gap: 18px;
  }
  .mark-dot { width: 60px; height: 60px; border-radius: 50%; background: var(--yellow); }
  .mark-name { color: var(--ink-light); font-size: 38px; font-weight: 600; }
  .web-line {
    position: absolute; left: 0; right: 0; bottom: 26px; text-align: center;
    color: var(--ink-soft); font-size: 17px; letter-spacing: 2.6px;
  }

  /* back with name */
  .big-name {
    position: absolute; left: 0; right: 0; top: 98px; text-align: center;
    color: var(--ink-grey); font-size: 52px; font-weight: 600; line-height: 1;
  }
</style>
</head>
<body>
<main class="sheet">

  <section class="card card--front" aria-label="Card front">
    <p class="front-name">The Kestrel Works</p>
  </section>

  <section class="card card--contact" aria-label="Contact side">
    <span class="contact-bar"></span>
    <h1 class="person-name">Your Name</h1>
    <p class="person-title">Title</p>
    <p class="address">00, Complex name<br>City, State 0042</p>
    <ul class="details">
      <li><svg viewBox="0 0 10 10" aria-hidden="true"><path d="M2 0.5 L3.8 2.6 L2.9 3.7 C3.6 5.2 4.8 6.4 6.3 7.1 L7.4 6.2 L9.5 8 L8.2 9.5 C4 9 1 6 0.5 1.8 Z"/></svg>0987 654321</li>
      <li><svg viewBox="0 0 10 10" aria-hidden="true"><path d="M1 4 L2.5 1.5 H7.5 L9 4 V8 H7.5 V7 H2.5 V8 H1 Z"/></svg>0987 654321</li>
      <li><svg viewBox="0 0 10 10" aria-hidden="true"><path d="M0.5 2 H9.5 V8.5 H0.5 Z M1 2.5 L5 5.5 L9 2.5" stroke="#262626" stroke-width="0.8"/></svg>info@kestrelworks.com</li>
    </ul>
    <p class="web-small">www.kestrel<span class="accent">works</span>.com</p>
    <p class="contact-name">The Kestrel Works</p>
  </section>

  <section class="card card--back-mark" aria-label="Card back with mark">
    <div class="mark-row">
      <span class="mark-dot"></span>
      <p class="mark-name">The Kestrel Works</p>
    </div>
    <p class="web-line">www.kestrelworks.com</p>
  </section>

  <section class="card card--back-name" aria-label="Card back with name">
    <p class="big-name">The Kestrel Works</p>
    <p class="web-line">www.kestrelworks.com</p>
  </section>

</main>
</body>
</html>
```